Event Website for the Audio & Visual Industry

Convene is an exhibition aimed at meeting the business needs of audio and visual professionals – the visitors are the ones that make purchase decisions when buying anything to do with AV installation, Lighting & Entertainment Technology, DJ Technologies and even Musical Instruments.

We need to rebuild our website to reflect the professional look but with a bit of creativity/flare that is associated with the industry.

Websites whose design is along the lines we're looking for:

• http:www.pelmora.com.au
• http:www.kavrin.com
• http://www.brightpanelfair.net/ (competitor expo, like the layout. Not fantastic though, but the best I’ve seen from the industry)
• http://www.tuvelo.com.au and http://www.ostrand.com.au/ (Like these brand websites, they are clean and corporate but the use of imagery allows it to have some personality)

Target Market(s)

Corporate AV End Users, Lighting Designers, Concert/Entertainment companies, Sound Engineers

Industry/Entity Type

Business

Requirements
Must have
• Refer to the current splash page – www.convene-expo.com
This is the look and feel we have developed for our brochure. We want to expand on this and create a professional corporate look and feel without alienating existing sound, light and vision sectors.

The website's focus is to register visitors to attend the show. Please include a floating 'Register Free' Call to action. Please also include floating social media buttons. For what I mean by 'floating' check out the Social media buttons on this website: http://quorvix.com/2012/02/19/tall-boat-preview/ (scroll down to see effect).

We'll like to include a Rotating Banner at the top.

Sponsor element at the bottom off the page.

Sign up form functionality

Menu to be: About the Show, What's On, Register, How to Exhibit, Blog, Contact us.

I would like to see designs for a content page as well as the homepage.

```html
<!DOCTYPE html>
<html lang="en">
<head>
<meta charset="utf-8">
<title>Convene 2012</title>
<link rel="stylesheet" href="https://fonts.googleapis.com/css2?family=PT+Sans:wght@400;700&family=Arimo:wght@400;700&display=swap">
<style>
  :root {
    --ink: #111;
    --text: #666;
    --muted: #888;
    --red: #d7141f;
    --panel: #eeeeee;
    --line: #c8c8c8;
    --nav-top: #8a8a8a;
    --nav-bottom: #5d5d5d;
    --nav-text: #e4e4e4;
    --photo-dark: #0b0b0a;
    --photo-gold: #c9903a;
  }
  * { box-sizing: border-box; margin: 0; padding: 0; }
  html, body { width: 1200px; height: 929px; overflow: hidden; background: #fff; }
  body { font-family: "Arimo", Arial, sans-serif; color: var(--text); }
  .page { position: relative; width: 1160px; height: 898px; transform: scale(1.0345); transform-origin: 0 0; }
  .abs { position: absolute; }
  .nowrap { white-space: nowrap; }

  /* header */
  .brand { left: 93px; top: 62px; display: flex; align-items: center; gap: 10px; }
  .brand-dot { width: 14px; height: 14px; border-radius: 50%; background: var(--red); }
  .brand-name { font-family: "PT Sans", sans-serif; font-size: 44px; color: var(--ink); line-height: 1; white-space: nowrap; }

  .partner { left: 605px; top: 62px; width: 160px; }
  .partner-lead { font-size: 10px; font-style: italic; color: #444; }
  .partner-name { font-family: "PT Sans", sans-serif; font-size: 18px; color: var(--red); line-height: 1.1; margin-top: 8px; white-space: nowrap; }
  .header-rule { left: 773px; top: 55px; width: 1px; height: 58px; background: var(--line); }
  .event-info { left: 790px; top: 55px; white-space: nowrap; }
  .event-date { font-size: 24px; color: var(--muted); letter-spacing: .5px; }
  .event-venue { font-size: 13px; font-weight: 700; color: #777; line-height: 17px; margin-top: 2px; }

  /* navigation */
  .main-nav { left: 91px; top: 151px; width: 980px; height: 41px; border-radius: 6px;
    background: linear-gradient(var(--nav-top), var(--nav-bottom)); box-shadow: 0 2px 3px rgba(0,0,0,.25);
    display: flex; padding-left: 208px; }
  .main-nav a { color: var(--nav-text); text-decoration: none; font-size: 13px; display: flex; align-items: center; justify-content: center;
    border-left: 1px solid #4d4d4d; box-shadow: inset 1px 0 0 #969696; }
  .main-nav a:nth-child(1) { width: 162px; } .main-nav a:nth-child(2) { width: 128px; }
  .main-nav a:nth-child(3) { width: 118px; } .main-nav a:nth-child(4) { width: 152px; }
  .main-nav a:nth-child(5) { width: 93px; } .main-nav a:nth-child(6) { width: 119px; }

  /* hero */
  .hero-frame { left: 97px; top: 211px; width: 566px; height: 339px; background: #fff; padding: 5px;
    box-shadow: 0 0 4px rgba(0,0,0,.3); }
  .hero-photo { width: 100%; height: 100%;
    background: radial-gradient(ellipse 60% 45% at 50% 55%, #f4d48a 0%, var(--photo-gold) 35%, #3a2410 70%, var(--photo-dark) 100%); }
  .hero-title { left: 697px; top: 242px; font-family: "PT Sans", sans-serif; font-weight: 400; font-size: 20px; line-height: 21px;
    color: var(--ink); letter-spacing: .6px; text-transform: uppercase; white-space: nowrap; }
  .hero-copy { left: 698px; top: 342px; font-size: 13.5px; line-height: 21px; letter-spacing: .2px; white-space: nowrap; }

  .signup { left: 698px; top: 484px; width: 372px; height: 64px; background: var(--panel); padding: 7px 16px; }
  .signup-label { font-family: "PT Sans", sans-serif; font-size: 13px; color: #666; text-transform: uppercase; letter-spacing: .5px; }
  .signup-input { position: absolute; left: 16px; top: 26px; width: 262px; height: 26px; border: 1px solid #ccc; background: #fff; }
  .signup-go { position: absolute; left: 291px; top: 25px; width: 36px; height: 28px; border-radius: 8px; border: 1px solid #ddd;
    background: linear-gradient(#fff, #e4e4e4); font-size: 12px; color: #555; display: flex; align-items: center; justify-content: center; }

  /* floating tab */
  .float-tab { left: 1074px; top: 205px; width: 76px; height: 292px; background: #fff; border: 2px solid #c9c9c9; border-radius: 6px;
    box-shadow: 0 1px 3px rgba(0,0,0,.2); text-align: center; padding-top: 12px; }
  .float-small { font-size: 13px; color: #666; line-height: 14px; }
  .float-big { font-size: 18px; font-weight: 700; color: #777; line-height: 19px; }
  .float-sep { width: 54px; margin: 6px auto 10px; border-top: 2px dotted #999; }
  .social-list { display: flex; flex-direction: column; align-items: center; gap: 9px; margin-top: 9px; }
  .social-list span { width: 18px; height: 18px; border-radius: 2px; }

  /* feature row */
  .card { top: 577px; height: 198px; border-radius: 6px; border: 1px solid #ddd;
    background: linear-gradient(#fff, #e9e9e9); box-shadow: 0 1px 3px rgba(0,0,0,.15); padding: 6px; }
  .card-inner { height: 100%; border-radius: 4px; background: linear-gradient(#fafafa, #e6e6e6); padding: 16px 14px; }
  .card-title { font-family: "PT Sans", sans-serif; font-weight: 400; font-size: 17px; line-height: 19px; color: var(--ink);
    letter-spacing: .4px; text-transform: uppercase; white-space: nowrap; }
  .highlights { list-style: none; margin-top: 17px; }
  .highlights li { font-size: 14px; font-weight: 700; color: #555; letter-spacing: .6px; line-height: 22px; display: flex; align-items: center; gap: 6px; }
  .topics { font-size: 12px; line-height: 18px; color: #666; margin-top: 14px; white-space: nowrap; }

  .action { left: 760px; width: 310px; height: 60px; border-radius: 6px; border: 1px solid #ddd; background: #fff;
    box-shadow: 0 1px 3px rgba(0,0,0,.15); padding: 4px; }
  .action-inner { height: 100%; border-radius: 4px; background: linear-gradient(#f4f4f4, #e1e1e1);
    display: flex; align-items: center; gap: 10px; padding-left: 12px; white-space: nowrap;
    font-family: "PT Sans", sans-serif; font-size: 16px; color: #777; letter-spacing: .3px; text-transform: uppercase; }

  /* footer */
  .footer-rule { left: 91px; width: 979px; height: 1px; background: var(--line); }
  .copyright { left: 91px; top: 821px; font-size: 11px; color: #555; }
  .contact { right: 90px; top: 812px; text-align: right; font-size: 11px; line-height: 16px; color: #555; white-space: nowrap; }
  .notice { left: 0; top: 862px; width: 1160px; text-align: center; font-size: 10px; line-height: 15px; color: #444; }
</style>
</head>
<body>
<div class="page">

  <header>
    <div class="abs brand">
      <span class="brand-dot"></span><span class="brand-name">Convene 2012</span>
    </div>
    <div class="abs partner">
      <div class="partner-lead">in association with</div>
      <div class="partner-name">Avorum International</div>
    </div>
    <div class="abs header-rule"></div>
    <div class="abs event-info">
      <div class="event-date">21st-23rd August 2012</div>
      <div class="event-venue">Harbourside Convention &amp; Exhibition Center,<br>Wattle Quay, Australia</div>
    </div>
  </header>

  <nav class="abs main-nav">
    <a href="#">About the Show</a><a href="#">What's On</a><a href="#">Register</a>
    <a href="#">How to Exhibit</a><a href="#">Blog</a><a href="#">Contact us</a>
  </nav>

  <section>
    <div class="abs hero-frame"><div class="hero-photo" role="img" aria-label="Harbour opera house lit gold at night, reflected in the water"></div></div>
    <h1 class="abs hero-title">Austrailia's largest audio<br>visual, entertainment &amp;<br>information communications<br>technology event</h1>
    <p class="abs hero-copy">With over 500 brands on display, Convene in asso-<br>ciation with Avorum International, brings together<br>the worlds of ICT, integrating all areas including<br>Visual, Education, Entertainment, Audio &amp; Lighting<br>Technology, Worship, Digital Signage and Unified<br>Communications.</p>
    <form class="abs signup">
      <div class="signup-label">Sign up for the news letter</div>
      <div class="signup-input"></div>
      <div class="signup-go">GO</div>
    </form>
  </section>

  <aside class="abs float-tab">
    <svg width="34" height="30" viewBox="0 0 34 30" aria-hidden="true">
      <rect x="3" y="5" width="20" height="22" rx="3" fill="none" stroke="#555" stroke-width="3"/>
      <path d="M14 19 L27 4 L31 8 L18 22 L13 23 Z" fill="#3d8fd0"/>
    </svg>
    <div class="float-small">Register</div>
    <div class="float-big">FREE</div>
    <div class="float-sep"></div>
    <div class="float-small">Follow</div>
    <div class="float-big" style="font-size:15px">US</div>
    <div class="social-list">
      <span style="background:#3b5998"></span>
      <span style="background:#4fc3e8"></span>
      <span style="background:#2a77b0"></span>
      <span style="background:#222"></span>
      <span style="background:#c8211f"></span>
    </div>
  </aside>

  <section>
    <div class="abs card" style="left:91px;width:310px">
      <div class="card-inner">
        <h2 class="card-title">Be part of Austrailia's only<br>event for the audio visual &amp;<br>entertainment industry</h2>
        <ul class="highlights">
          <li><svg width="12" height="10" viewBox="0 0 12 10"><path d="M0 5H9M6 1L10 5L6 9" stroke="#d7141f" stroke-width="2" fill="none"/></svg>NEW LOCATION</li>
          <li><svg width="12" height="10" viewBox="0 0 12 10"><path d="M0 5H9M6 1L10 5L6 9" stroke="#d7141f" stroke-width="2" fill="none"/></svg>EVEN BIGGER SHOW</li>
          <li><svg width="12" height="10" viewBox="0 0 12 10"><path d="M0 5H9M6 1L10 5L6 9" stroke="#d7141f" stroke-width="2" fill="none"/></svg>NEW SEMINARS</li>
          <li><svg width="12" height="10" viewBox="0 0 12 10"><path d="M0 5H9M6 1L10 5L6 9" stroke="#d7141f" stroke-width="2" fill="none"/></svg>EVEN MORE SURPRISE</li>
        </ul>
      </div>
    </div>
    <div class="abs card" style="left:426px;width:309px">
      <div class="card-inner">
        <h2 class="card-title" style="margin-top:6px">Discover teh latest advance-<br>ments in ........</h2>
        <p class="topics">• Concert Production • AV Installation • Broad-<br>cast • Staging • Lighting &amp; Entertainment Tech-<br>nology • Digital Media &amp; Information Services •<br>Education Technology • Post Production • Multi-<br>media • Audio Engineering • Recording • DJ<br>Technologies • Musical Instruments</p>
      </div>
    </div>

    <a class="abs action" style="top:577px"><div class="action-inner">
      <svg width="28" height="28" viewBox="0 0 28 28"><circle cx="14" cy="14" r="13" fill="#fff" stroke="#ddd"/><path d="M14 7V19M9 14L14 19L19 14" stroke="#bbb" stroke-width="3" fill="none"/></svg>
      Download the floor plan</div></a>
    <a class="abs action" style="top:647px"><div class="action-inner">
      <svg width="28" height="28" viewBox="0 0 28 28"><circle cx="14" cy="14" r="13" fill="#fff" stroke="#ddd"/><rect x="7" y="9" width="14" height="10" fill="none" stroke="#bbb" stroke-width="2"/><path d="M7 9L14 15L21 9" stroke="#bbb" stroke-width="2" fill="none"/></svg>
      Contact the convene team</div></a>
    <a class="abs action" style="top:717px"><div class="action-inner">
      <svg width="28" height="28" viewBox="0 0 28 28"><circle cx="14" cy="14" r="13" fill="#fff" stroke="#ddd"/><path d="M9 20L11 15L19 7L22 10L14 18Z" fill="none" stroke="#bbb" stroke-width="2"/></svg>
      Sign up for the newsletter</div></a>
  </section>

  <footer>
    <div class="abs footer-rule" style="top:804px"></div>
    <div class="abs copyright">© 2012 Tandrel Exhibitions, Austrlia. All rights reserved.</div>
    <div class="abs contact">Mezzanine level, 118 Colbert Street, Sydney, NSW 2000, Australia.<br>Telephone: +61 2 9000 4821. Facsimile: +61 2 9000 4822.</div>
    <div class="abs footer-rule" style="top:848px"></div>
    <p class="abs notice">STRICTLY TRADE ONLY. Entry is restricted to members of the ICT, Audio Visual and Entertainment industries.<br>Persons not in these categories, including children will not be admitted at any time.</p>
  </footer>

</div>
</body>
</html>
```